Animal Eye Clinic needs a Business card

We are a new veterinary ophthalmology practice (Ridgeline Pet Vision Care) and we need a business card designed. We only see animal eyes - we are not a regular veterinary clinic. We already have a logo. We are looking for a professional, good looking business card to hand out to our clients. We are looking for something simple but professional and contemporary. Our logo is likely the only picture/graphic that needs to be on the card.
Updates

Contact Information for Business Card

Delia Vossman, BSc, DVM, MSc, DipACVO
Veterinary Ophthalmologist

Phone: 250.418.3927
Email: ridgelinepetvisioncare@mailbox-example.net
Website: ridgelinepetvisioncare-example.net
Address: 1874 Thornbury Rd
Kelowna, BC, V1X 4M9

Colors

Designer to choose colors to be used in the design.

Requirements
Must have
• Our logo (attached)

```html
<!DOCTYPE html>
<html lang="en">
<head>
<meta charset="utf-8">
<title>Ridgeline Pet Vision Care – Business Card</title>
<link href="https://fonts.googleapis.com/css2?family=Roboto:wght@400;500;700&display=swap" rel="stylesheet">
<style>
  :root {
    --backdrop: #c6c6c6;
    --teal: #0096a8;
    --teal-deep: #0a7484;
    --teal-light: #3fb0bf;
    --ink: #555555;
    --paper: #ffffff;
    --slate: #7a7a7a;
  }
  * { margin: 0; padding: 0; box-sizing: border-box; }
  html, body {
    width: 1200px; height: 794px; overflow: hidden;
    background: var(--backdrop);
    font-family: "Roboto", Arial, sans-serif;
  }
  .card {
    position: absolute; top: 267px;
    width: 454px; height: 261px; overflow: hidden;
    box-shadow: 0 2px 4px rgba(0,0,0,.25);
  }
  .card--front { left: 141px; background: var(--paper); }
  .card--back { left: 601px; background: var(--teal); }

  /* front */
  .brand { position: absolute; left: 20px; top: 30px; display: flex; align-items: center; gap: 10px; }
  .brand__dot { width: 46px; height: 46px; border-radius: 50%; background: var(--teal); }
  .brand__name { color: var(--teal); font-weight: 500; font-size: 15px; letter-spacing: .2px; }

  .person { position: absolute; left: 20px; top: 95px; }
  .person__name { color: var(--teal); font-weight: 700; font-size: 16px; letter-spacing: .1px; text-transform: uppercase; }
  .person__creds { color: var(--teal); font-size: 12px; margin-top: 2px; }
  .person__role { color: var(--ink); font-size: 12px; margin-top: 3px; }

  .contact { position: absolute; left: 21px; top: 162px; list-style: none; }
  .contact li { display: flex; align-items: center; gap: 3px; color: var(--ink); font-size: 12px; line-height: 16.5px; }
  .contact svg { width: 9px; height: 9px; fill: var(--teal); flex: none; }

  .address-band {
    position: absolute; left: 0; top: 224px; width: 359px; height: 22px;
    background: var(--teal);
    clip-path: polygon(0 0, 339px 0, 359px 100%, 0 100%);
    color: var(--paper); font-size: 12px; line-height: 22px; padding-left: 24px;
  }
  .front-art {
    position: absolute; left: 330px; top: 9px;
    width: 268px; height: 268px; border-radius: 50%;
    background: radial-gradient(circle at 40% 60%, var(--teal-light), var(--teal) 60%);
  }

  /* back */
  .back-art {
    position: absolute; left: 0; top: 0; width: 130px; height: 261px;
    background: linear-gradient(160deg, var(--teal-deep) 0%, var(--teal-light) 70%, var(--teal) 100%);
    opacity: .7;
    -webkit-mask-image: linear-gradient(90deg, #000 60%, transparent);
    mask-image: linear-gradient(90deg, #000 60%, transparent);
  }
  .back-name {
    position: absolute; right: 34px; top: 188px;
    color: var(--paper); font-weight: 500; font-size: 21px; letter-spacing: .2px;
  }
</style>
</head>
<body>

<section class="card card--front">
  <div class="front-art" role="img" aria-label="Illustration of dog, cat and horse silhouettes inside a teal circle"></div>

  <div class="brand">
    <span class="brand__dot"></span>
    <span class="brand__name">Ridgeline Pet Vision Care</span>
  </div>

  <div class="person">
    <h1 class="person__name">Delia Vossman</h1>
    <p class="person__creds">BSc, DVM, MSc, DipACVO</p>
    <p class="person__role">Veterinary Ophthalmologist</p>
  </div>

  <ul class="contact">
    <li><svg viewBox="0 0 24 24"><path d="M6.6 10.8a15 15 0 0 0 6.6 6.6l2.2-2.2a1 1 0 0 1 1-.25 11.4 11.4 0 0 0 3.6.57 1 1 0 0 1 1 1V20a1 1 0 0 1-1 1A17 17 0 0 1 3 4a1 1 0 0 1 1-1h3.5a1 1 0 0 1 1 1c0 1.25.2 2.45.57 3.6a1 1 0 0 1-.25 1z"/></svg>250.418.3927</li>
    <li><svg viewBox="0 0 24 24"><path d="M2 5h20v14H2z M2 5l10 7 10-7" stroke="#fff" stroke-width="1.5"/></svg>ridgelinepetvisioncare@mailbox-example.net</li>
    <li><svg viewBox="0 0 24 24"><circle cx="12" cy="12" r="10"/><path d="M2 12h20M12 2c3 3 3 17 0 20M12 2c-3 3-3 17 0 20" stroke="#fff" stroke-width="1.5" fill="none"/></svg>ridgelinepetvisioncare-example.net</li>
  </ul>

  <div class="address-band">1874 Thornbury Rd, Kelowna, BC, V1X 4M9</div>
</section>

<section class="card card--back">
  <div class="back-art" role="img" aria-label="Faint tone-on-tone horse and cat silhouettes"></div>
  <p class="back-name">Ridgeline Pet Vision Care</p>
</section>

</body>
</html>
```